Business Cards - Brightpath Horizon

need to design unique business card for my mortgage business. I need to design credit card style business card for my business or any unique idea that you might have

Target Market(s)

Home Loan customers

Industry/Entity Type

Mortgage Brokerage

Contact Information for Business Card

please design credit card style or very unique style business card

Colors

Designer to choose colors to be used in the design.

Requirements
Must have
• Name
• position
• Phone number
• fax number
• email address
• website address
• social media address
• All above fields will be provided once design in finalised

```html
<!DOCTYPE html>
<html lang="en">
<head>
<meta charset="utf-8">
<title>Brightpath Horizon – Business Cards</title>
<link href="https://fonts.googleapis.com/css2?family=Libre+Baskerville:wght@400&display=swap" rel="stylesheet">
<style>
  :root {
    --backdrop: #2a2a2a;
    --card-white: #ffffff;
    --brand-blue: #0530c4;
    --brand-orange: #ff8c14;
    --text-light: #ffffff;
    --card-shadow: rgba(0,0,0,0.55);
  }
  * { margin: 0; padding: 0; box-sizing: border-box; }
  html, body { width: 1200px; height: 960px; overflow: hidden; }
  body {
    background: var(--backdrop);
    font-family: "Libre Baskerville", "Times New Roman", serif;
    position: relative;
  }
  .card {
    position: absolute;
    width: 600px;
    height: 343px;
    border-radius: 18px;
    overflow: hidden;
    box-shadow: 2px 4px 6px var(--card-shadow);
  }
  .card--front { left: 314px; top: 113px; background: var(--card-white); }
  .card--back { left: 311px; top: 472px; background: var(--brand-orange); }

  .front__brand {
    position: absolute;
    left: 33px;
    top: 92px;
    display: flex;
    align-items: center;
    gap: 10px;
  }
  .brand-dot {
    width: 18px; height: 18px; border-radius: 50%;
    background: var(--brand-orange);
  }
  .front__brand .brand-name {
    font-size: 26px;
    color: var(--brand-blue);
    letter-spacing: 0.5px;
  }
  .front__rule {
    position: absolute; left: 0; top: 208px;
    width: 100%; height: 3px; background: var(--brand-blue);
  }
  .front__band {
    position: absolute; left: 0; top: 213px;
    width: 100%; height: 130px; background: var(--brand-blue);
    color: var(--text-light);
  }
  .contact-list {
    list-style: none;
    position: absolute; left: 33px; top: 26px;
    font-size: 13px; line-height: 19.3px;
  }
  .contact-list li { display: flex; align-items: center; gap: 8px; }
  .contact-list svg { width: 14px; height: 14px; fill: var(--text-light); flex: none; }
  .person {
    position: absolute; right: 35px; top: 42px; text-align: right;
  }
  .person__name { font-size: 19px; letter-spacing: 0.3px; }
  .person__role { font-size: 14px; margin-top: 3px; }

  .back__brand {
    position: absolute; left: 0; top: 140px; width: 100%;
    display: flex; justify-content: center; align-items: center; gap: 12px;
  }
  .back__brand .brand-dot { background: var(--text-light); width: 22px; height: 22px; }
  .back__brand .brand-name { font-size: 36px; color: var(--text-light); }
  .social {
    position: absolute; top: 280px; left: 242px;
    display: flex; gap: 3px;
  }
  .social span {
    width: 27px; height: 27px; border-radius: 50%; background: var(--text-light);
  }
</style>
</head>
<body>
  <section class="card card--front" aria-label="Card front">
    <div class="front__brand">
      <span class="brand-dot"></span>
      <span class="brand-name">Brightpath Horizon</span>
    </div>
    <div class="front__rule"></div>
    <div class="front__band">
      <ul class="contact-list">
        <li><svg viewBox="0 0 16 16"><path d="M3 1l3 3-2 2c1 2 3 4 5 5l2-2 3 3-2 2C7 14 2 9 1 3z"/></svg>555 214 7730</li>
        <li><svg viewBox="0 0 16 16"><path d="M4 1h8v4H4zM1 6h14v6h-3v3H4v-3H1zM5 10v4h6v-4z"/></svg>555 214 7731</li>
        <li><svg viewBox="0 0 16 16"><path d="M1 4h14v9H1zM2 5l6 4 6-4v1l-6 4-6-4z" fill-rule="evenodd"/></svg>info@brightpath.com</li>
        <li><svg viewBox="0 0 16 16"><circle cx="8" cy="8" r="7"/><path d="M5 4c2 1 1 3 3 3s1 3 3 4M10 2c-1 2 1 3 3 3" stroke="#0530c4" stroke-width="1.5" fill="none"/></svg>www.brightpath.com</li>
      </ul>
      <div class="person">
        <div class="person__name">DANIEL REYES</div>
        <div class="person__role">CEO/FOUNDER</div>
      </div>
    </div>
  </section>

  <section class="card card--back" aria-label="Card back">
    <div class="back__brand">
      <span class="brand-dot"></span>
      <span class="brand-name">Brightpath Horizon</span>
    </div>
    <div class="social" aria-label="Social media links">
      <span></span><span></span><span></span><span></span>
    </div>
  </section>
</body>
</html>
```